Creative, fresh business card design for Ripplecraft Facades

We need a fresh, creative business card design for Ripplecraft Facades. We are the manufacturer of Ripplecraft Facades in Australia. Wall panels are 2400 x 1200mm panels made from MDF and feature 3D patterns on the face of the panel. The colours to be used are green, silver/grey and white RGB
Red 187
Green 207
Blue 65.

An idea is to possibly use a watermark of one of our designs as a background (like on the "Grids" design on the left hand side of page 2 of our brochure).

Target Market(s)

Interior designers, architects, builders and home renovators

Industry/Entity Type

Business

Contact Information for Business Card

Details to go on the card are:
Our logo (attached),
Slogan: "Decorative panels for interiors and exteriors",
Contact name,
Position,
Mobile phone number,
Business address,
Business phone,
Business fax,
Website and
Email address.

I have attached a few images of our panels and our brochure for reference.

The colours of the business card should feature our logo colours which are: RGB
Red 187
Green 207
Blue 65

Requirements
Must have
• Very modern fonts and design. Some of the designs shown especially the "Prisms" design which is a popular design.
Nice to have
• Creative but simple design. Very contemporary.
Should not have
• Anything ornate or old fashioned.

```html
<!DOCTYPE html>
<html lang="en">
<head>
<meta charset="utf-8">
<title>Ripplecraft Facades – Business Card</title>
<link rel="stylesheet" href="https://fonts.googleapis.com/css2?family=Open+Sans:wght@400;600;700&display=swap">
<style>
  :root {
    --brand-green: #bbcf41;
    --brand-grey: #8e8f91;
    --ink: #555658;
    --card-white: #f4f4f4;
    --page: #e6e6e4;
  }
  * { box-sizing: border-box; margin: 0; padding: 0; }
  html, body { width: 1200px; height: 900px; overflow: hidden; }
  body {
    background: var(--page);
    font-family: "Open Sans", Arial, sans-serif;
    position: relative;
  }
  .card {
    position: absolute;
    width: 560px;
    height: 320px;
    background: var(--card-white);
    box-shadow: 0 6px 18px rgba(0,0,0,0.18);
    overflow: hidden;
  }

  /* Front */
  .card-front { left: 60px; top: 90px; }
  .panel-texture {
    position: absolute; inset: 0;
    background: radial-gradient(circle at 50% 45%, #ffffff 0%, #ececec 55%, #dedede 100%);
  }
  .front-brand {
    position: absolute; left: 0; right: 0; top: 105px;
    display: flex; align-items: center; justify-content: center; gap: 14px;
  }
  .brand-square { width: 34px; height: 34px; background: var(--brand-green); }
  .brand-name {
    color: var(--brand-green);
    font-weight: 700;
    font-size: 34px;
    letter-spacing: -0.5px;
  }
  .slogan {
    position: absolute; left: 0; right: 0; top: 175px;
    text-align: center;
    color: var(--brand-green);
    font-weight: 700;
    font-size: 17px;
    line-height: 1.2;
    text-transform: uppercase;
  }

  /* Back */
  .card-back { left: 580px; top: 490px; }
  .wave { position: absolute; left: 0; bottom: 0; width: 560px; height: 160px; }
  .back-brand {
    position: absolute; right: 30px; top: 40px;
    display: flex; align-items: center; gap: 8px;
  }
  .back-brand .brand-square { width: 18px; height: 18px; }
  .back-brand .brand-name { font-size: 19px; }
  .contact-block { position: absolute; left: 40px; top: 30px; color: var(--ink); }
  .person-name { color: var(--brand-green); font-weight: 700; font-size: 19px; }
  .person-role { font-size: 12px; margin-top: 2px; }
  .address { font-size: 13px; line-height: 1.5; margin-top: 20px; margin-left: 8px; }
  .contact-list { list-style: none; margin-top: 12px; margin-left: 8px; font-size: 13px; line-height: 1.55; }
  .contact-list li { display: flex; align-items: center; gap: 8px; }
  .contact-list svg { width: 12px; height: 12px; fill: var(--brand-green); }
  .website {
    position: absolute; right: 24px; bottom: 62px;
    color: #ffffff; font-weight: 600; font-size: 12px;
  }
</style>
</head>
<body>

<section class="card card-front">
  <div class="panel-texture" role="img" aria-label="Faint pyramid wall panel pattern in white and light grey"></div>
  <div class="front-brand">
    <span class="brand-square"></span>
    <span class="brand-name">Ripplecraft Facades</span>
  </div>
  <p class="slogan">Decorative panels for<br>interiors and exteriors</p>
</section>

<section class="card card-back">
  <svg class="wave" viewBox="0 0 560 160" preserveAspectRatio="none" aria-hidden="true">
    <path d="M0 122 C160 120 340 82 480 4 C340 76 160 108 0 110 Z" fill="var(--brand-grey)"/>
    <path d="M0 136 C180 134 400 92 560 14 L560 160 L0 160 Z" fill="var(--brand-green)"/>
  </svg>

  <div class="back-brand">
    <span class="brand-square"></span>
    <span class="brand-name">Ripplecraft Facades</span>
  </div>

  <div class="contact-block">
    <h1 class="person-name">Marcus Ellery</h1>
    <p class="person-role">Managing Director</p>
    <p class="address">48 Tannery Lane,<br>Geelong VIC 3220</p>
    <ul class="contact-list">
      <li><svg viewBox="0 0 12 12"><path d="M1 4 Q6 0 11 4 L10 6 L8 5 L8 4 Q6 3 4 4 L4 5 L2 6 Z M3 7 H9 L10 11 H2 Z"/></svg>(03) 5210 4418</li>
      <li><svg viewBox="0 0 12 12"><path d="M3 1 H9 V4 H3 Z M1 5 H11 V10 H1 Z"/></svg>(03) 5210 4419</li>
      <li><svg viewBox="0 0 12 12"><path d="M3 0 H9 V12 H3 Z M4 1.5 V9 H8 V1.5 Z"/></svg>0412 870 356</li>
      <li><svg viewBox="0 0 12 12"><path d="M0 2 H12 V10 H0 Z M0.5 2.5 L6 7 L11.5 2.5" stroke="#fff" stroke-width="0.8"/></svg>hello@ripplecraft.com.au</li>
    </ul>
  </div>

  <p class="website">www.ripplecraft.com.au</p>
</section>

</body>
</html>
```